Graphic Design of Business Process

We require an eye-catching, sophisticated design of 2 business processes (attached), that will be used digitally AND for print (to be put on walls in our office).

The basic layout is attached. We require a creative, professional designer to re-design these so that they look appealing but still able to grasp all the information.

We will require vector files and editable project files for final delivery. You may refer to our website (quillharbourworks.com.au) for an indication of our brand.

If you have any questions, please ask.

Thank you.

```html
<!DOCTYPE html>
<html lang="en">
<head>
<meta charset="utf-8">
<title>Content Hierarchy</title>
<link rel="stylesheet" href="https://fonts.googleapis.com/css2?family=Josefin+Sans:wght@700&family=Oswald:wght@600&display=swap">
<style>
  :root {
    --sky: #a9dcf5;
    --sky-light: #eaf6fd;
    --ink: #111111;
    --gold: #fbb040;
    --blue: #4254a6;
    --blue-deep: #2e4799;
    --blue-ring: #3f4a8a;
    --purple: #b8479a;
    --purple-deep: #7b2468;
    --purple-ring: #8f3a7c;
    --orange: #f7941d;
    --orange-light: #fdb93f;
    --orange-ring: #b57a2c;
    --pink: #ec1e79;
    --card: #f4f5f6;
    --card-shade: #e4e5e7;
  }
  html, body { margin: 0; padding: 0; overflow: hidden; }
  body {
    width: 1200px; height: 1050px;
    background: radial-gradient(ellipse at 50% 45%, #ffffff 30%, var(--sky-light) 60%, var(--sky) 100%);
    position: relative;
  }
  .hierarchy-graphic { position: absolute; inset: 0; width: 1200px; height: 1050px; }
  .title {
    font-family: "Josefin Sans", sans-serif; font-weight: 700;
    font-size: 64px; fill: var(--ink);
  }
  .tier-name, .tier-role {
    font-family: "Oswald", sans-serif; font-weight: 600;
    text-anchor: middle;
  }
  .tier-name { font-size: 46px; }
  .tier-role { font-size: 50px; }
  .wordmark {
    font-family: "Josefin Sans", sans-serif; font-weight: 700;
    font-size: 26px; letter-spacing: 6px; fill: var(--ink); text-anchor: middle;
  }
  .blue { fill: var(--blue); }
  .purple { fill: var(--purple); }
  .orange { fill: var(--orange); }
</style>
</head>
<body>
<svg class="hierarchy-graphic" viewBox="0 0 1200 1050" xmlns="http://www.w3.org/2000/svg">
  <defs>
    <linearGradient id="titlePanel" x1="0" y1="0" x2="0" y2="1">
      <stop offset="0" stop-color="#d6eefb"/>
      <stop offset="1" stop-color="#eef8fe"/>
    </linearGradient>
  </defs>

  <!-- Title panel -->
  <path d="M190 0 H1010 V188 Q1010 228 970 228 H230 Q190 228 190 188 Z" fill="url(#titlePanel)"/>
  <text class="title" x="600" y="172" text-anchor="middle">CONTENT HIERARCHY</text>
  <rect x="242" y="188" width="716" height="9" fill="var(--gold)"/>

  <!-- Cards -->
  <g class="cards">
    <rect x="95" y="470" width="310" height="436" fill="var(--card)"/>
    <rect x="445" y="470" width="310" height="436" fill="var(--card)"/>
    <rect x="795" y="470" width="310" height="436" fill="var(--card)"/>
    <polygon points="250,570 405,480 405,665" fill="var(--card-shade)" opacity="0.7"/>
    <polygon points="600,570 755,480 755,665" fill="var(--card-shade)" opacity="0.7"/>
    <polygon points="950,570 1105,480 1105,665" fill="var(--card-shade)" opacity="0.7"/>

    <path d="M95 828 L160 890 H340 L405 828 V906 H95 Z" fill="var(--blue)"/>
    <path d="M445 828 L510 890 H690 L755 828 V906 H445 Z" fill="var(--purple)"/>
    <path d="M795 828 L860 890 H1040 L1105 828 V906 H795 Z" fill="var(--orange)"/>
  </g>

  <!-- Ribbon -->
  <polygon points="75,465 75,380 130,348 430,348 430,465" fill="var(--blue-deep)"/>
  <rect x="430" y="348" width="60" height="117" fill="var(--blue-deep)"/>
  <rect x="700" y="348" width="140" height="117" fill="var(--purple-deep)"/>
  <polygon points="1060,348 1070,348 1125,380 1125,465 1060,465" fill="var(--orange-light)"/>
  <polygon points="75,380 130,348 130,465 75,465" fill="#26377e"/>

  <!-- Connector lines -->
  <g fill="none" stroke-width="6" stroke-linecap="round">
    <line x1="305" y1="290" x2="425" y2="362" stroke="var(--purple)"/>
    <line x1="425" y1="362" x2="545" y2="290" stroke="var(--blue)"/>
    <line x1="655" y1="290" x2="775" y2="362" stroke="var(--pink)"/>
    <line x1="775" y1="362" x2="895" y2="290" stroke="var(--purple)"/>
    <line x1="305" y1="562" x2="425" y2="488" stroke="var(--purple)"/>
    <line x1="425" y1="488" x2="545" y2="562" stroke="var(--blue)"/>
    <line x1="655" y1="562" x2="775" y2="488" stroke="var(--pink)"/>
    <line x1="775" y1="488" x2="895" y2="562" stroke="var(--purple)"/>
  </g>

  <!-- Hero hexagon -->
  <g class="tier tier-hero">
    <polygon points="250,274 378,348 378,496 250,570 122,496 122,348" fill="var(--blue)"/>
    <polygon points="250,294 361,358 361,486 250,550 139,486 139,358" fill="var(--blue-ring)"/>
    <polygon points="250,310 347,366 347,478 250,534 153,478 153,366" fill="#ffffff"/>
    <text class="tier-name blue" x="250" y="438">HERO</text>
  </g>

  <!-- Hub hexagon -->
  <g class="tier tier-hub">
    <polygon points="600,274 728,348 728,496 600,570 472,496 472,348" fill="var(--purple)"/>
    <polygon points="600,294 711,358 711,486 600,550 489,486 489,358" fill="var(--purple-ring)"/>
    <polygon points="600,310 697,366 697,478 600,534 503,478 503,366" fill="#ffffff"/>
    <text class="tier-name purple" x="600" y="438">HUB</text>
  </g>

  <!-- Hygiene hexagon -->
  <g class="tier tier-hygiene">
    <polygon points="950,274 1078,348 1078,496 950,570 822,496 822,348" fill="var(--orange)"/>
    <polygon points="950,294 1061,358 1061,486 950,550 839,486 839,358" fill="var(--orange-ring)"/>
    <polygon points="950,310 1047,366 1047,478 950,534 853,478 853,366" fill="#ffffff"/>
    <text class="tier-name orange" x="950" y="438">HYGIENE</text>
  </g>

  <!-- Tier roles -->
  <text class="tier-role blue" x="250" y="688">TENTPOLE</text>
  <text class="tier-role blue" x="250" y="748">CAMPAIGNS</text>

  <text class="tier-role purple" x="600" y="688">REGULAR</text>
  <text class="tier-role purple" x="600" y="750">“PUSH”</text>
  <text class="tier-role purple" x="600" y="812">CONTENT</text>

  <text class="tier-role orange" x="950" y="688">ALWAYS-ON</text>
  <text class="tier-role orange" x="950" y="750">“PULL”</text>
  <text class="tier-role orange" x="950" y="812">CONTENT</text>

  <!-- Brand name -->
  <text class="wordmark" x="600" y="988">QUILL HARBOUR WORKS</text>
</svg>
</body>
</html>
```